Road Construction Company needs business cards

We would like a new business card designed for our business.

We're a road construction company based in Qld, Australia.

Can the business card please have the following information on it.

Name: Warren Halbeck
Position: General Manager
Phone: 0472 915 348
Email: Warren.halbeck@tovrin.com.au
Address: 87 Marrow Ave, Pendlebay, QLD, 4023
Website: www.tovrin.com.au

Visually we'd like the card to be professional and simple.

Attached is our logo.

Our website is www.tovrin.com.au

Target Market(s)

Men aged 25-60

Contact Information for Business Card

As listed in project description

Font styles to use
Serif

Requirements
Must have
• Large logo on back of card

```html
<!DOCTYPE html>
<html lang="en">
<head>
<meta charset="utf-8">
<title>Tovrin Business Card</title>
<link rel="stylesheet" href="https://fonts.googleapis.com/css2?family=Michroma&family=Saira:wght@400;800&display=swap">
<style>
  :root {
    --backdrop: #2b2b2b;
    --brand-blue: #0455a4;
    --sky-blue: #34a6d8;
    --sky-deep: #2a93c9;
    --paper: #ffffff;
  }
  html, body {
    margin: 0;
    padding: 0;
    width: 1093px;
    height: 1200px;
    overflow: hidden;
    background: var(--backdrop);
  }
  .canvas {
    position: relative;
    width: 1093px;
    height: 1200px;
  }
  .card {
    position: absolute;
    left: 264px;
    width: 579px;
    height: 357px;
    overflow: hidden;
  }
  .card--front { top: 226px; background: var(--brand-blue); color: var(--paper); }
  .card--back { top: 620px; background: var(--paper); }

  .feature-panel {
    position: absolute;
    left: 302px;
    top: 0;
    right: 0;
    bottom: 0;
    background: linear-gradient(180deg, var(--sky-blue) 0%, #5bb8e2 45%, #eaf6fc 70%, var(--sky-deep) 100%);
  }
  .wordmark {
    font-family: "Saira", sans-serif;
    font-weight: 800;
    line-height: 1;
    margin: 0;
  }
  .card--front .wordmark {
    position: absolute;
    left: 30px;
    top: 56px;
    font-size: 38px;
    letter-spacing: 0.2em;
    color: var(--paper);
  }
  .person { position: absolute; left: 27px; top: 142px; }
  .person__name {
    font-family: "Michroma", sans-serif;
    font-size: 16px;
    font-weight: 400;
    letter-spacing: 0.02em;
    margin: 0;
    line-height: 1;
    -webkit-text-stroke: 1.1px var(--paper);
  }
  .person__role {
    font-family: "Saira", sans-serif;
    font-size: 15.5px;
    margin: 3px 0 0;
  }
  .address {
    position: absolute;
    left: 27px;
    top: 194px;
    font-family: "Saira", sans-serif;
    font-style: normal;
    font-size: 16px;
    line-height: 21px;
  }
  .contacts {
    position: absolute;
    left: 27px;
    top: 256px;
    margin: 0;
    padding: 0;
    list-style: none;
    font-family: "Saira", sans-serif;
    font-size: 16px;
    line-height: 21px;
  }
  .contacts li { display: flex; align-items: center; gap: 7px; }
  .contacts svg { width: 15px; height: 15px; flex: none; }

  .card--back .wordmark {
    position: absolute;
    left: 0;
    right: 0;
    top: 146px;
    padding-left: 0.22em;
    text-align: center;
    font-size: 60px;
    letter-spacing: 0.22em;
    color: var(--brand-blue);
  }
</style>
</head>
<body>
<main class="canvas">
  <section class="card card--front" aria-label="Business card front">
    <div class="feature-panel" role="img" aria-label="Large brand decoration in light blue and white"></div>
    <p class="wordmark">TOVRIN</p>
    <div class="person">
      <h1 class="person__name">WARREN HALBECK</h1>
      <p class="person__role">General Manager</p>
    </div>
    <address class="address">87 Marrow Ave<br>Pendlebay, QLD, 4023</address>
    <ul class="contacts">
      <li>
        <svg viewBox="0 0 16 16" aria-hidden="true"><path fill="#fff" d="M3.5 1.5l2.2 2.8-1.2 1.6c.8 1.9 2.1 3.3 4 4.2l1.6-1.2 2.8 2.2-1.2 2.4C6.8 13.2 2.8 9.2 1.4 3.3z"/></svg>
        0472 915 348
      </li>
      <li>
        <svg viewBox="0 0 16 16" aria-hidden="true"><path fill="#fff" d="M1 3.5h14v9H1z"/><path fill="none" stroke="#0455a4" stroke-width="1.2" d="M1 3.5l7 5.5 7-5.5M1 12.5l5-4.5M15 12.5l-5-4.5"/></svg>
        Warren.halbeck@tovrin.com.au
      </li>
      <li>
        <svg viewBox="0 0 16 16" aria-hidden="true"><g fill="none" stroke="#fff" stroke-width="1.2"><circle cx="8" cy="8" r="6.5"/><ellipse cx="8" cy="8" rx="2.8" ry="6.5"/><path d="M1.5 8h13M2.6 4.5h10.8M2.6 11.5h10.8"/></g></svg>
        www.tovrin.com.au
      </li>
    </ul>
  </section>

  <section class="card card--back" aria-label="Business card back">
    <p class="wordmark">TOVRIN</p>
  </section>
</main>
</body>
</html>
```